Satchel & Sundial needs new business card design

I need a new business card design. I'm looking for out-of-the-box design which represents the freedom of being a location independent entrepreneur.
I offer coaching, retreats and trips.
I would like to see designs with and without the photo.
Colors I use are black (#000000), green (#25A796) and brown (#D7C38C)
Website satchelandsundial.example

Target Market(s)

location independent entrepreneurs, digital nomads, people looking to swap the 9 to 5 for a lifestyle business

Industry/Entity Type

Business

Contact Information for Business Card

Dorota Falkner
Your Lifestyle Business Coach, Retreat & Trip Leader
http://satchelandsundial.example
hello@satchelandsundial.example
Live a life you don't need a holiday from

Font styles to use
Serif
Sans Serif

Requirements
Must have
• One side should contain only the logo. I would also consider having the "Live a life you don't need a holiday from" on that side too (depending on how it looks)
• Please show both sides on the designs.

```html
<!DOCTYPE html>
<html lang="en">
<head>
<meta charset="utf-8">
<title>Satchel &amp; Sundial — Business Card</title>
<link rel="stylesheet" href="https://fonts.googleapis.com/css2?family=Source+Sans+3:wght@400;600&display=swap">
<style>
  :root {
    --backdrop: #141414;
    --card-light: #f3f3f3;
    --brand-green: #25a796;
    --ink: #1a1a1a;
    --white: #ffffff;
  }
  * { margin: 0; padding: 0; box-sizing: border-box; }
  html, body {
    width: 1200px;
    height: 900px;
    overflow: hidden;
    background: var(--backdrop);
    font-family: "Source Sans 3", "Myriad Pro", Arial, sans-serif;
  }
  .stage { position: relative; width: 1200px; height: 900px; }

  .card {
    position: absolute;
    top: 184px;
    height: 490px;
    border-radius: 12px;
    text-align: center;
  }
  .card--front { left: 299px; width: 301px; background: var(--card-light); }
  .card--back  { left: 645px; width: 305px; background: var(--brand-green); }

  .wordmark {
    position: absolute;
    left: 0; right: 0;
    font-weight: 600;
    font-size: 24px;
    letter-spacing: 1.5px;
    text-transform: uppercase;
  }
  .card--front .wordmark { top: 298px; top: 112px; color: var(--ink); }
  .card--back .wordmark  { top: 208px; color: var(--white); }

  .holder-name {
    position: absolute; left: 0; right: 0; top: 252px;
    font-size: 17px; font-weight: 600; color: var(--brand-green);
  }
  .holder-role {
    position: absolute; left: 0; right: 0; top: 278px;
    font-size: 13.5px; line-height: 18px; color: var(--ink);
  }
  .contact-list {
    position: absolute; left: 0; right: 0; top: 331px;
    list-style: none;
    font-size: 13.5px; line-height: 18px; color: var(--ink);
  }
  .contact-list li { display: flex; justify-content: center; align-items: center; gap: 7px; }
  .contact-list svg { width: 9px; height: 9px; flex: none; }

  .tagline {
    position: absolute; left: 40px; right: 40px; top: 384px;
    font-size: 13.5px; line-height: 18px;
    text-transform: uppercase; color: var(--brand-green);
  }

  .services {
    position: absolute; left: 0; right: 0; top: 360px;
    font-size: 15px; font-weight: 600; color: var(--white);
    letter-spacing: 0.2px;
  }
</style>
</head>
<body>
<main class="stage">
  <section class="card card--front" aria-label="Business card front">
    <div class="wordmark">Satchel &amp; Sundial</div>
    <h1 class="holder-name">Dorota Falkner</h1>
    <p class="holder-role">Your Lifestyle Business Coach<br>Retreat &amp; Trip Leader</p>
    <ul class="contact-list">
      <li>
        <svg viewBox="0 0 10 10" aria-hidden="true"><rect x="0.5" y="2" width="9" height="6.5" fill="#25a796"/><path d="M0.5 2 L5 5.5 L9.5 2" fill="none" stroke="#f3f3f3" stroke-width="1"/></svg>
        hello@satchelandsundial.example
      </li>
      <li>
        <svg viewBox="0 0 10 10" aria-hidden="true"><circle cx="5" cy="5" r="4.5" fill="#25a796"/><path d="M2.5 3.5 Q4 2.5 5 4 T7.5 6" fill="none" stroke="#f3f3f3" stroke-width="1"/></svg>
        www.satchelandsundial.example
      </li>
    </ul>
    <p class="tagline">Live a life you don't need a holiday from</p>
  </section>

  <section class="card card--back" aria-label="Business card back">
    <div class="wordmark">Satchel &amp; Sundial</div>
    <p class="services">COACHING | RETREATS | TRIPS</p>
  </section>
</main>
</body>
</html>
```